Local massage therapist needs some new marketing material

Hi there! I am a massage therapist here in Denver, CO in Alder Bend(shopping and art district) of the city. My business is called Lumo Bodywork of Denver. My practice has an eastern influence and I do reflexology, thai massage and use Chinese herbs, etc. I know all my clients and pay close attention to details. I am also very respectful of tradition and it shows in how I work. I tend to like modern, clean, fun, Asian designs. I am wanting a new business card and brochure. I have a logo and branding for my business that I want used in the design. Currently, the sign for my building is purple and I think my logo was designed to be purple. I will attach pictures of it and can send whatever files are necessary so it can be integrated into the brochure, etc. I like the purple but open to using other colors as well. Thanks!
My website is lumobodyworkofdenver.example where info can be gathered about me and services/fees for brochure.
Updates

Just increased budget. Please see new feedback in discussion thread.

Thanks!

                                       HEY ALL,

Just wanted to let you know that I made a change to my website. It is on the Prices Page. I no longer have the frequent  flyer prices but I added discounts. Let me know if you have any questions. Thanks so much!

Target Market(s)

healthy, urban, educated, upper middle class, yogis

Industry/Entity Type

Marketing

Requirements
Must have
• logo stays purple
Should not have
• not too busy

```html
<!DOCTYPE html>
<html lang="en">
<head>
<meta charset="UTF-8">
<title>Lumo Bodywork of Denver – Business Card</title>
<link rel="stylesheet" href="https://fonts.googleapis.com/css2?family=Open+Sans:ital,wght@0,400;0,600;0,700;1,400&display=swap">
<style>
  :root {
    --purple: #6a2c91;
    --purple-soft: #8a5bb0;
    --ink: #555558;
    --ink-light: #7a7a7e;
    --rule: #9a9a9e;
    --card: #ffffff;
    --backdrop: #ecebe8;
  }
  * { margin: 0; padding: 0; box-sizing: border-box; }
  html, body { width: 1200px; height: 720px; overflow: hidden; }
  body {
    background: var(--backdrop);
    font-family: "Open Sans", Arial, sans-serif;
    color: var(--ink);
    position: relative;
  }
  .card {
    position: absolute;
    top: 200px;
    width: 560px;
    height: 320px;
    background: var(--card);
    box-shadow: 0 2px 8px rgba(0,0,0,0.12);
    overflow: hidden;
  }
  .card--front { left: 27px; }
  .card--back { left: 613px; }

  /* Front */
  .name-band {
    position: absolute; left: 0; right: 0; top: 40px; height: 44px;
    background: var(--purple);
    display: flex; align-items: center; justify-content: center;
    color: #fff; font-weight: 700; font-size: 17px; letter-spacing: 0.3px;
  }
  .name-band .title { font-size: 11px; font-weight: 400; margin-left: 5px; margin-top: 3px; }
  .band-rule { position: absolute; left: 0; right: 0; height: 1px; background: var(--rule); }
  .band-rule--top { top: 32px; }
  .band-rule--bottom { top: 92px; }

  .brand { position: absolute; display: flex; flex-direction: column; align-items: center; }
  .brand__mark {
    width: 58px; height: 58px; border-radius: 50%;
    background: var(--purple-soft);
  }
  .brand__name {
    margin-top: 12px; color: var(--purple);
    font-weight: 400; font-size: 44px; letter-spacing: 8px; line-height: 1;
  }
  .card--front .brand { left: 50px; top: 128px; width: 190px; }

  .divider { position: absolute; left: 268px; top: 112px; width: 1px; height: 150px; background: #c9c9cc; }
  .contact { position: absolute; left: 284px; top: 118px; right: 14px; list-style: none; font-size: 12.5px; color: var(--ink); }
  .contact li { display: flex; align-items: center; height: 23px; white-space: nowrap; }
  .contact svg { width: 13px; height: 13px; margin-right: 6px; flex: none; }
  .contact .address { margin-top: 10px; }

  /* Back */
  .card--back .brand { right: 30px; top: 18px; align-items: flex-end; }
  .card--back .brand__mark { width: 48px; height: 48px; margin-right: 46px; }
  .card--back .brand__name { font-size: 36px; letter-spacing: 6px; margin-top: 8px; }

  .appointment { position: absolute; left: 32px; top: 120px; right: 30px; }
  .appointment__heading {
    color: var(--purple); font-weight: 700; font-size: 13px; letter-spacing: 0.3px;
    display: flex; align-items: flex-end; gap: 8px;
  }
  .appointment__heading::after { content: ""; flex: 1; border-bottom: 1px solid var(--rule); margin-bottom: 14px; }
  .field-row { display: flex; align-items: flex-end; font-size: 14px; margin-top: 14px; white-space: nowrap; }
  .field-line { display: inline-block; border-bottom: 1px solid var(--rule); height: 1px; margin: 0 8px 4px; }
  .hours { margin-top: 18px; font-size: 15px; line-height: 1.35; color: var(--ink); }
  .notice { margin-top: 12px; font-size: 14px; font-style: italic; color: var(--ink-light); }
</style>
</head>
<body>

<section class="card card--front" aria-label="Card front">
  <div class="band-rule band-rule--top"></div>
  <div class="name-band">YOUR NAME,<span class="title">TITLE</span></div>
  <div class="band-rule band-rule--bottom"></div>

  <div class="brand">
    <span class="brand__mark"></span>
    <span class="brand__name">LUMO</span>
  </div>

  <div class="divider"></div>

  <ul class="contact">
    <li>
      <svg viewBox="0 0 16 16" aria-hidden="true"><circle cx="8" cy="8" r="8" fill="#555558"/><path d="M5.2 4.2l1.4-.3.8 1.9-.9.7a5 5 0 0 0 2.9 2.9l.7-.9 1.9.8-.3 1.4c-3.7.3-6.8-2.8-6.5-6.5z" fill="#fff"/></svg>
      303.555.0148
    </li>
    <li>
      <svg viewBox="0 0 16 16" aria-hidden="true"><circle cx="8" cy="8" r="8" fill="#555558"/><rect x="4" y="5.2" width="8" height="5.6" fill="#fff"/><path d="M4 5.2l4 3 4-3" fill="none" stroke="#555558" stroke-width="0.9"/></svg>
      info@lumobodyworkofdenver.example
    </li>
    <li>
      <svg viewBox="0 0 16 16" aria-hidden="true"><circle cx="8" cy="8" r="8" fill="#555558"/><circle cx="8" cy="8" r="4.2" fill="none" stroke="#fff" stroke-width="0.9"/><ellipse cx="8" cy="8" rx="1.8" ry="4.2" fill="none" stroke="#fff" stroke-width="0.9"/><path d="M3.8 8h8.4" stroke="#fff" stroke-width="0.9"/></svg>
      www.lumobodyworkofdenver.example
    </li>
    <li class="address">1470 E Alder Ave, Alderton, CO 80299</li>
  </ul>
</section>

<section class="card card--back" aria-label="Card back">
  <div class="brand">
    <span class="brand__mark"></span>
    <span class="brand__name">LUMO</span>
  </div>

  <div class="appointment">
    <h2 class="appointment__heading">YOUR APPOINTMENT</h2>
    <div class="field-row">
      Name :<span class="field-line" style="width:120px"></span>
      Time :<span class="field-line" style="width:100px"></span>am / pm
    </div>
    <div class="field-row">
      Date :<span class="field-line" style="width:140px"></span>
    </div>
    <p class="hours">Tues - Fri 10am - 8pm Sat 10am-5pm<br>(Appointments required) No walk-ins please.</p>
    <p class="notice">We appreciate a 24 hr. notice for cancellations</p>
  </div>
</section>

</body>
</html>
```